Salon and Spa Distributor Business Card

Need a business card. We are are distributor in the salon and spa industry. We identify with natural beauty. Need a card with:
Company Name: Petal Quarry"
Title: "President & CEO"
Address
Company Phone number
email
website
Tag Line:" Your Natural Salon Partner"

Industry/Entity Type

Business

Contact Information for Business Card

Name: Dov Strommen
Title: "President & CEO"
Address: 31 Harlow Ln, Bexmoor, NJ 07813
Company Phone number: 800-463-5918
email: dovstrommen@petalquarry.example
website: www.petalquarry.example

Requirements
Should not have
• No black backgrounds

```html
<!DOCTYPE html>
<html lang="en">
<head>
<meta charset="utf-8">
<title>Petal Quarry – Business Card</title>
<link rel="stylesheet" href="https://fonts.googleapis.com/css2?family=Questrial&family=Raleway:wght@700&display=swap">
<style>
  :root {
    --page-bg: #ecebe7;
    --card-white: #ffffff;
    --brand-green: #5cb547;
    --brand-green-dark: #2f9640;
    --brand-green-light: #62bd46;
    --name-green: #7cc242;
    --ink: #222222;
    --ink-soft: #444444;
    --rule: #555555;
  }
  * { box-sizing: border-box; margin: 0; padding: 0; }
  html, body {
    width: 1200px;
    height: 1000px;
    overflow: hidden;
    background: var(--page-bg);
    font-family: "Questrial", "Century Gothic", sans-serif;
  }
  .canvas {
    position: relative;
    width: 1200px;
    height: 1000px;
  }
  .card {
    position: absolute;
    left: 320px;
    width: 560px;
    height: 320px;
    border-radius: 30px;
    overflow: hidden;
    box-shadow: 0 6px 18px rgba(0,0,0,0.18);
  }
  /* Front */
  .card-front {
    top: 110px;
    background: var(--card-white);
  }
  .brand {
    position: absolute;
    top: 58px;
    left: 230px;
    display: flex;
    align-items: center;
    gap: 12px;
  }
  .brand-dot {
    width: 40px;
    height: 40px;
    border-radius: 50%;
    background: var(--brand-green);
    flex: none;
  }
  .brand-name {
    font-size: 30px;
    color: var(--brand-green);
    white-space: nowrap;
  }
  .top-rule {
    position: absolute;
    left: 268px;
    right: 0;
    top: 150px;
    border-top: 1px solid var(--rule);
  }
  .person {
    position: absolute;
    left: 34px;
    top: 178px;
  }
  .person-name {
    font-family: "Raleway", "Century Gothic", sans-serif;
    font-weight: 700;
    font-size: 22px;
    color: var(--ink);
    white-space: nowrap;
  }
  .person-name .surname { color: var(--name-green); }
  .person-title {
    font-size: 15px;
    color: var(--ink-soft);
    margin-top: 3px;
  }
  .name-rule {
    position: absolute;
    left: 204px;
    right: 30px;
    top: 192px;
    border-top: 1px solid var(--rule);
  }
  .address {
    position: absolute;
    right: 32px;
    top: 210px;
    text-align: right;
    font-style: normal;
    font-size: 15px;
    line-height: 1.35;
    color: var(--ink-soft);
  }
  .contact {
    position: absolute;
    left: 34px;
    bottom: 28px;
    list-style: none;
    font-size: 15px;
    line-height: 1.3;
    color: var(--ink-soft);
  }
  /* Back */
  .card-back {
    top: 530px;
    background: radial-gradient(ellipse at 55% 55%, var(--brand-green-light) 0%, var(--brand-green) 55%, var(--brand-green-dark) 100%);
  }
  .back-brand {
    position: absolute;
    left: 30px;
    top: 110px;
    width: 130px;
    display: flex;
    flex-direction: column;
    align-items: center;
    gap: 10px;
  }
  .back-brand .brand-dot { background: var(--card-white); width: 56px; height: 56px; }
  .back-brand .brand-name { color: var(--card-white); font-size: 19px; }
  .tagline {
    position: absolute;
    left: 178px;
    top: 126px;
    font-size: 21px;
    color: var(--card-white);
    white-space: nowrap;
  }
</style>
</head>
<body>
<main class="canvas">
  <section class="card card-front" aria-label="Business card front">
    <div class="brand">
      <span class="brand-dot"></span>
      <span class="brand-name">Petal Quarry</span>
    </div>
    <div class="top-rule"></div>
    <div class="person">
      <p class="person-name">Dov <span class="surname">Strommen</span></p>
      <p class="person-title">President &amp; CEO</p>
    </div>
    <div class="name-rule"></div>
    <address class="address">
      31 Harlow Ln<br>Bexmoor, NJ 07813
    </address>
    <ul class="contact">
      <li>800 - 463 - 5918</li>
      <li>dovstrommen@petalquarry.example</li>
      <li>www.petalquarry.example</li>
    </ul>
  </section>

  <section class="card card-back" aria-label="Business card back">
    <div class="back-brand">
      <span class="brand-dot"></span>
      <span class="brand-name">Petal Quarry</span>
    </div>
    <p class="tagline">“Your Natural Salon Partner”</p>
  </section>
</main>
</body>
</html>
```